Business Card & Letterhead Design

We a financial advice company based in Australia. We provide advice to wealthy farmers.

We are changing our business name FROM Brightvale Financial TO Tallowmere Wealth and we need a new letterhead and double sided business card design

Attached is designs from our previous branding (Brightvale Financial) as it includes all the details we require on the new Tallowmere Wealth business cards and letterhead.

Need extra days to review

```html
<!DOCTYPE html>
<html lang="en">
<head>
<meta charset="utf-8">
<title>Tallowmere Wealth Letterhead</title>
<link rel="stylesheet" href="https://fonts.googleapis.com/css2?family=Open+Sans:wght@400;600&display=swap">
<style>
  :root {
    --bg: #e4e4e4;
    --paper: #ffffff;
    --ink: #2b2b2b;
    --ink-soft: #555555;
    --band: #4a4a4a;
    --band-text: #ffffff;
  }
  * { margin: 0; padding: 0; box-sizing: border-box; }
  html, body { width: 1040px; height: 1200px; overflow: hidden; background: var(--bg); }
  body { font-family: "Open Sans", sans-serif; color: var(--ink); position: relative; }
  .letterhead {
    position: absolute; left: 78px; top: 31px; width: 884px; height: 1137px;
    background: var(--paper); box-shadow: 0 2px 10px rgba(0,0,0,0.12);
  }
  .brand-name {
    position: absolute; left: 83px; top: 74px;
    font-size: 20px; font-weight: 400; color: var(--ink);
    white-space: nowrap; line-height: 1;
  }
  .sender { position: absolute; right: 92px; top: 34px; text-align: right; font-size: 14px; line-height: 20.5px; color: var(--ink); font-style: normal; }
  .sender p + p { margin-top: 3px; }
  .sender b { font-weight: 600; }
  .letter-body { position: absolute; left: 83px; top: 262px; width: 716px; font-size: 14px; color: var(--ink-soft); }
  .issue-date { margin-bottom: 18px; }
  .recipient { line-height: 17.5px; margin-bottom: 48px; }
  .salutation { margin-bottom: 28px; }
  .paragraph { line-height: 25.8px; text-align: justify; margin-bottom: 25px; }
  .closing { margin-top: 50px; }
  .signatory { margin-top: 63px; }
  .signatory-name { font-size: 16.5px; font-weight: 600; color: var(--ink); }
  .signatory-role { margin-top: 4px; }
  .footer-lines { position: absolute; left: 123px; right: 98px; top: 1023px; display: flex; justify-content: space-between; font-size: 13px; font-weight: 600; text-transform: uppercase; color: var(--ink); }
  .footer-band { position: absolute; left: 0; right: 0; bottom: 0; height: 84px; background: var(--band); color: var(--band-text); text-align: center; font-size: 14.5px; font-weight: 600; line-height: 21.5px; padding-top: 9px; padding-left: 100px; }
</style>
</head>
<body>
  <main class="letterhead">
    <header>
      <div class="brand-name">Tallowmere Wealth</div>
      <address class="sender">
        <p>Marlow Ridge Investments Pty Ltd&nbsp; ATF The Ashcombe<br>Investment Trust T/AS Brightvale Financial<br><b>ABN:</b> 00 123 456 789</p>
        <p>Corporate Authorised Representative<br>Of Keystone Advice Partners Limited<br>Suite 4A, 18 Wattle St Riverbend QLD 4000<br>PO Box 1234 Riverbend QLD 4000</p>
        <p><b>P:</b> (07) 3000 1100 | <b>F:</b> (07) 3000 1199<br><b>E:</b> hello@brightvalefinancial.com.au<br><b>W:</b> www.brightvalefinancial.com.au</p>
      </address>
    </header>
    <section class="letter-body">
      <p class="issue-date">Issuing Date: May 5, 2018</p>
      <p class="recipient">Name Of Employee Mr. XYZABC<br>Address of Employee<br>Address Line 2 etc..</p>
      <p class="salutation">Dear Mr.XYZABC</p>
      <p class="paragraph">Lorem Ipsum has been the industry's standard dummy text ever since the 1500s, when an unknown printer took a galley of type and scrambled it to make a type specimen book. It has survived not only five centuries, but also the leap into electronic typesetting, remaining essentially unchanged. It was popularised in the 1960s with the release of Letraset sheets containing Lorem Ipsum passages, and more recently with desktop publishing software like Aldus PageMaker including versions of Lorem Ipsum.</p>
      <p class="paragraph">Lorem Ipsum is simply dummy text of the printing and typesetting industry. Lorem Ipsum has been the industry's standard dummy text ever since the 1500s, when an unknown printer took a galley of type and scrambled it to make a type specimen book.</p>
      <p class="paragraph">It has survived not only five centuries, but also the leap into electronic typesetting, remaining essentially unchanged. It was popularised in the 1960s with the release of Letraset sheets containing Lorem IpsumIpsum passages.</p>
      <p class="closing">Yours Sincerely</p>
      <div class="signatory">
        <p class="signatory-name">Daniel Marsh</p>
        <p class="signatory-role">Managing Director</p>
      </div>
    </section>
    <footer>
      <div class="footer-lines"><span>‘Financial Peace of Mind’</span><span>A Referral Built Business</span></div>
      <div class="footer-band">
        Keystone Advice Partners Limited&nbsp; | ABN 00 987 654 321<br>
        Australian&nbsp; Financial Services License | License Number 000000<br>
        Principle Address: 120 Harbour Rd. PO Box 5500 Eastport VIC 3000
      </div>
    </footer>
  </main>
</body>
</html>
```